Southern Plantskills Academy needs a modern website that oozes professionalism

Our current website is boring and looks like everyone elses. We need a modern website that says we are the best at plant operator training. We use Brontovex and Hiraketo equipment for our training. We train all over Australia in Civil Construction, Mining and Quarrying. We want to be the "Go to" website for all plant operator training in Australia.

Industry/Entity Type

Heavy Machinery Training

Colors
0054AA
0677BA
7BADD7
CADEEF
E8F1F8
FFF300
FFF600
FEFA6F
FFFEC7
FFFEE8

```html
<!DOCTYPE html>
<html lang="en">
<head>
<meta charset="utf-8">
<title>Southern Plantskills Academy</title>
<link href="https://fonts.googleapis.com/css2?family=Open+Sans:wght@400;600;700;800&display=swap" rel="stylesheet">
<style>
:root{
  --navy:#0b2148;
  --navy-deep:#081a3a;
  --heading:#0f2f5f;
  --yellow:#f6c31a;
  --yellow-soft:#ffe36a;
  --olive:#9aa23a;
  --ink:#4a4f58;
  --muted:#8a8f98;
  --light:#f2f3f5;
  --white:#ffffff;
}
*{margin:0;padding:0;box-sizing:border-box}
html,body{width:1200px;height:4368px;overflow:hidden}
body{font-family:"Open Sans",Arial,sans-serif;color:var(--ink);background:var(--white);position:relative}
.abs{position:absolute}
.btn{position:absolute;background:var(--yellow);color:var(--white);font-weight:700;font-size:13px;letter-spacing:.5px;display:flex;align-items:center;justify-content:center;border-radius:3px;text-transform:uppercase}
.eyebrow{font-size:15px;font-weight:600;color:var(--yellow)}
.section-title{font-size:44px;font-weight:700;line-height:1.15}

/* header */
.site-header{position:absolute;left:0;top:0;width:1200px;height:72px;background:var(--white)}
.topbar{position:absolute;left:400px;top:0;width:800px;height:30px;background:var(--navy);font-size:12px;color:var(--white);display:flex;align-items:center}
.topbar span{position:absolute;display:flex;align-items:center;gap:6px}
.topbar .badge{background:var(--yellow);padding:4px 14px;font-weight:700;top:5px;left:280px}
.brand{position:absolute;left:110px;top:18px;display:flex;align-items:center;gap:10px;font-weight:800;font-size:17px;color:var(--heading);line-height:1.1}
.brand-mark{width:30px;height:30px;background:var(--yellow);border-radius:50%}
.nav{position:absolute;left:395px;top:46px;display:flex;gap:42px;font-size:13px;font-weight:600;color:var(--heading)}
.nav-cta{position:absolute;left:930px;top:44px;width:124px;height:26px;border:1.5px solid var(--yellow);color:var(--yellow);font-size:11px;font-weight:700;display:flex;align-items:center;justify-content:center;border-radius:3px}

/* hero */
.hero{position:absolute;left:0;top:72px;width:1200px;height:760px;background:linear-gradient(120deg,#3a3a38 0%,#6b6357 45%,#4b4a45 70%,#2d2d2c 100%)}
.hero-text{position:absolute;left:110px;top:190px;color:var(--white)}
.hero-text .eyebrow{color:var(--white);font-size:14px}
.hero-text h1{font-size:46px;font-weight:700;line-height:1.25;margin-top:8px}
.hero-text p{font-size:13px;line-height:1.55;width:420px;margin-top:10px;opacity:.9}

/* about */
.collage{position:absolute;left:128px;top:905px;width:320px;height:320px;transform:rotate(45deg);background:linear-gradient(135deg,#3e5d86,#c9a15a 50%,#6a7d94);border:6px solid var(--white);box-shadow:0 0 0 2px #e5e8ee}
.about-text{position:absolute;left:632px;top:918px;width:470px}
.about-text h2{color:var(--heading);font-size:44px;font-weight:700;line-height:1.2;margin-top:10px}
.about-text p{font-size:14px;line-height:1.65;margin-top:20px;color:var(--muted)}

/* services */
.services{position:absolute;left:0;top:1440px;width:1200px;height:645px;background:var(--navy)}
.center{text-align:center;width:1200px;left:0}
.service-card{position:absolute;top:290px;width:320px;height:285px}
.service-photo{width:320px;height:200px;border-radius:6px 6px 0 0}
.service-label{position:absolute;left:20px;top:180px;width:280px;height:82px;background:var(--white);border-radius:6px;text-align:center;padding-top:16px}
.service-label h3{font-size:17px;font-weight:700;color:var(--heading)}
.service-label span{font-size:13px;color:var(--ink);display:block;margin-top:4px}
.service-icon{position:absolute;left:126px;top:-34px;width:68px;height:68px;border-radius:50%;background:var(--yellow);border:4px solid rgba(255,255,255,.35)}

/* reviews slider */
.reviews{position:absolute;left:0;top:2085px;width:1200px;height:620px;background:var(--light)}
.slide{position:absolute;top:200px;height:355px}
.slide-side-l{left:110px;width:225px;clip-path:polygon(35% 0,100% 0,100% 100%,35% 100%,0 50%);background:linear-gradient(160deg,#8b7a5c,#c4a23a 60%,#5c5649)}
.slide-side-r{left:850px;width:215px;clip-path:polygon(0 0,65% 0,100% 50%,65% 100%,0 100%);background:linear-gradient(160deg,#7d6f5a,#9b8a6c 60%,#4f4a42)}
.slide-main{left:355px;width:485px;background:linear-gradient(170deg,#8c9aa5,#5e6670 55%,#2f3338)}
.slide-caption{position:absolute;left:0;bottom:0;width:485px;height:105px;background:rgba(10,15,25,.55);color:var(--white);padding:14px 36px}
.slide-caption h4{font-size:16px;font-weight:700}
.slide-caption small{font-size:10px;opacity:.85}
.slide-caption p{font-size:10.5px;line-height:1.45;margin-top:6px;opacity:.9}

/* cta */
.cta{position:absolute;left:0;top:2705px;width:1200px;height:460px;background:linear-gradient(100deg,#15191f 0%,#2d3037 50%,#4a4d52 100%)}
.cta h2{position:absolute;left:110px;top:100px;font-size:44px;font-weight:700;line-height:1.25;color:var(--white);width:520px}
.pill{position:absolute;left:690px;width:395px;height:46px;border-radius:6px;background:rgba(120,120,124,.6);color:var(--white);font-size:12px;font-weight:600;display:flex;align-items:center;padding-left:40px}

/* testimonial cards */
.testi-card{position:absolute;top:3372px;width:318px;height:270px;background:var(--white);box-shadow:0 6px 22px rgba(20,30,60,.1)}
.avatar{position:absolute;left:-10px;top:-22px;width:98px;height:104px;background:linear-gradient(160deg,#d9dde2,#a8afb8)}
.testi-card h4{position:absolute;left:110px;top:12px;font-size:17px;font-weight:600;color:var(--heading)}
.testi-card .role{position:absolute;left:110px;top:40px;font-size:12px;color:var(--muted)}
.quote{position:absolute;right:20px;top:38px;font-size:70px;font-weight:800;color:var(--yellow);line-height:1}
.testi-card p{position:absolute;left:24px;top:112px;width:270px;font-size:13px;line-height:1.55;color:var(--ink)}

/* footer */
.footer{position:absolute;left:0;top:3830px;width:1200px;height:538px}
.footer-col{position:absolute;top:210px;color:var(--white)}
.footer-col h4{font-size:20px;font-weight:700}
.footer-col p{font-size:14px;line-height:1.5;font-weight:600}
.socials{display:flex;gap:12px;margin-top:26px}
.socials i{width:24px;height:24px;background:rgba(255,255,255,.16);display:block}
.subscribe{margin-top:16px;width:224px;height:38px;border-radius:4px;background:rgba(255,255,255,.14);font-size:12px;display:flex;align-items:center;justify-content:space-between;padding:0 10px 0 14px}
.contact-row{display:flex;gap:14px;margin-top:22px}
.contact-row b{display:block;font-size:15px}
.contact-row small{font-size:12px}
.bottom-bar{position:absolute;left:0;top:470px;width:1200px;height:68px;border-top:1px solid rgba(255,255,255,.15);color:var(--white);font-size:13px;font-weight:600;text-align:center;line-height:60px}
.to-top{position:absolute;left:1060px;top:490px;width:34px;height:34px;background:var(--yellow);border-radius:3px}
</style>
</head>
<body>

<header class="site-header">
  <div class="topbar">
    <span style="left:40px"><svg width="12" height="12" viewBox="0 0 24 24"><path d="M6 2l4 5-2 3a12 12 0 006 6l3-2 5 4-3 4C10 21 3 14 2 5z" fill="#f6c31a"/></svg>(02) 5550 3917</span>
    <span class="badge">Book a Training Course</span>
    <span style="left:600px"><svg width="12" height="12" viewBox="0 0 24 24"><path d="M12 2a7 7 0 017 7c0 5-7 13-7 13S5 14 5 9a7 7 0 017-7z" fill="#f6c31a"/><circle cx="12" cy="9" r="2.5" fill="#0b2148"/></svg>14 Quarry Lane, Dubbo</span>
  </div>
  <div class="brand"><span class="brand-mark"></span><span>SOUTHERN<br><small style="font-size:10px;font-weight:800">PLANTSKILLS ACADEMY</small></span></div>
  <nav class="nav"><span>Home</span><span>About Us</span><span>Services</span><span>Gallery</span><span>Our Team</span></nav>
  <div class="nav-cta">CONTACT US</div>
</header>

<section class="hero" role="img" aria-label="Large mining haul truck on a dusty quarry site">
  <div class="hero-text">
    <div class="eyebrow">Welcome</div>
    <h1>Empowering Operators,<br>Fueling Progress</h1>
    <p>Hands-on plant training delivered on real machines by experienced trainers, on sites right across Australia for every operator.</p>
  </div>
  <div class="btn" style="left:110px;top:452px;width:120px;height:34px;font-size:11px">Learn More</div>
  <svg class="abs" style="left:0;top:560px" width="1200" height="200" viewBox="0 0 1200 200">
    <path d="M0 140 C300 200 700 200 1200 40 L1200 200 L0 200Z" fill="#f6c31a"/>
    <path d="M0 160 C320 215 720 205 1200 70 L1200 200 L0 200Z" fill="#ffffff"/>
  </svg>
</section>

<div class="collage" role="img" aria-label="Diamond collage of operators and heavy machinery"></div>
<div class="about-text">
  <div class="eyebrow">Who We Are</div>
  <h2>Training Operators for Industry Leaders</h2>
  <p>We train plant operators across civil, mining and quarry work. Our courses use modern Brontovex and Hiraketo gear, giving every trainee real seat time and practical skills that employers trust on day one.</p>
  <p>Our assessors hold years of site experience and guide each learner from first start-up to confident, safe and certified operation, wherever the job may be across Australia.</p>
</div>
<div class="btn" style="left:632px;top:1296px;width:152px;height:40px">View More</div>

<section class="services">
  <div class="abs center" style="top:92px;color:#fff;font-size:15px;font-weight:600">What We Do</div>
  <h2 class="abs center section-title" style="top:120px;color:#fff">Services We Provide</h2>

  <div class="service-card" style="left:96px">
    <div class="service-photo" role="img" aria-label="Civil construction worker in hard hat on site" style="background:linear-gradient(150deg,#2d4e7a,#c78b3c 70%,#e0b45c)"></div>
    <div class="service-icon"></div>
    <svg class="abs" style="left:144px;top:-16px" width="32" height="32" viewBox="0 0 24 24"><path d="M12 3l2.7 5.6 6.1.9-4.4 4.3 1 6.1L12 17l-5.4 2.9 1-6.1-4.4-4.3 6.1-.9z" fill="none" stroke="#fff" stroke-width="1.6"/></svg>
    <div class="service-label"><h3>Civil Construction</h3><span>Read more &rarr;</span></div>
  </div>

  <div class="service-card" style="left:440px">
    <div class="service-photo" role="img" aria-label="Mining worker in high-visibility vest" style="background:linear-gradient(150deg,#d07a2e,#e8c9a0 60%,#b7a58a)"></div>
    <div class="service-icon"></div>
    <svg class="abs" style="left:144px;top:-16px" width="32" height="32" viewBox="0 0 24 24"><path d="M4 18h16M6 18a6 6 0 0112 0M12 8v4" fill="none" stroke="#fff" stroke-width="1.8"/></svg>
    <div class="service-label"><h3>Mining</h3><span>Read more &rarr;</span></div>
  </div>

  <div class="service-card" style="left:784px">
    <div class="service-photo" role="img" aria-label="Excavator working in a quarry" style="background:linear-gradient(150deg,#a8712c,#d8a550 55%,#7a5a32)"></div>
    <div class="service-icon"></div>
    <svg class="abs" style="left:144px;top:-16px" width="32" height="32" viewBox="0 0 24 24"><path d="M3 19h18M5 19v-5h8v5M13 14l4-6 3 3" fill="none" stroke="#fff" stroke-width="1.8"/></svg>
    <div class="service-label"><h3>Quarrying</h3><span>Read more &rarr;</span></div>
  </div>
</section>

<section class="reviews">
  <div class="abs center" style="top:92px;color:var(--olive);font-size:15px;font-weight:600">Testimonials</div>
  <h2 class="abs center section-title" style="top:115px;color:var(--heading)">Client Reviews</h2>
  <div class="slide slide-side-l" role="img" aria-label="Yellow loader at a work site"></div>
  <div class="slide slide-main" role="img" aria-label="Trainee operator in hard hat beside machinery">
    <div class="slide-caption">
      <h4>Lorem ipsum dolor sit amet</h4>
      <small>06.08.2023</small>
      <p>The trainers were patient and clear. I left with real confidence on the excavator and landed a site job within weeks.</p>
    </div>
  </div>
  <div class="slide slide-side-r" role="img" aria-label="Excavator loading a truck in a quarry"></div>
</section>

<section class="cta" role="img" aria-label="Heavy machinery silhouetted at dusk">
  <h2>Where Operators Thrive and Industries Flourish</h2>
  <div class="btn" style="left:110px;top:292px;width:146px;height:38px">Get Started</div>
  <div class="pill" style="top:136px">We're expert and certified staff</div>
  <div class="pill" style="top:198px">We're expert and certified staff</div>
  <div class="pill" style="top:260px">We're expert and certified staff</div>
</section>

<div class="abs center" style="top:3226px;color:var(--olive);font-size:15px;font-weight:600">Testimonials</div>
<h2 class="abs center section-title" style="top:3250px;color:var(--heading)">Client Reviews</h2>

<div class="testi-card" style="left:100px">
  <div class="avatar" role="img" aria-label="Portrait of a client"></div>
  <h4>Marcus Deller</h4><div class="role">CEO &amp; Founder</div><div class="quote">&ldquo;</div>
  <p>Every operator we hired from this academy arrived ready to work. Their practical focus shows from the very first shift on site.</p>
</div>
<div class="testi-card" style="left:442px">
  <div class="avatar" role="img" aria-label="Portrait of a client"></div>
  <h4>Marcus Deller</h4><div class="role">CEO &amp; Founder</div><div class="quote">&ldquo;</div>
  <p>Every operator we hired from this academy arrived ready to work. Their practical focus shows from the very first shift on site.</p>
</div>
<div class="testi-card" style="left:784px">
  <div class="avatar" role="img" aria-label="Portrait of a client"></div>
  <h4>Marcus Deller</h4><div class="role">CEO &amp; Founder</div><div class="quote">&ldquo;</div>
  <p>Every operator we hired from this academy arrived ready to work. Their practical focus shows from the very first shift on site.</p>
</div>

<div class="btn" style="left:524px;top:3712px;width:152px;height:40px">View More</div>

<footer class="footer">
  <svg class="abs" style="left:0;top:0" width="1200" height="538" viewBox="0 0 1200 538">
    <path d="M0 90 C350 -10 800 -10 1200 110 L1200 538 L0 538Z" fill="#f6c31a"/>
    <path d="M0 120 C360 20 820 20 1200 130 L1200 538 L0 538Z" fill="#0b2148"/>
  </svg>
  <div class="footer-col" style="left:110px;top:215px">
    <div style="display:flex;align-items:center;gap:10px;font-weight:800;font-size:16px;line-height:1.1"><span class="brand-mark"></span><span>SOUTHERN<br><small style="font-size:10px">PLANTSKILLS ACADEMY</small></span></div>
    <p style="margin-top:28px;width:250px">We have 14+ years experience Helping you overcome technology challenges</p>
    <div class="socials"><i></i><i></i><i></i><i></i></div>
  </div>
  <div class="footer-col" style="left:518px">
    <h4>Newsletter</h4>
    <p style="margin-top:22px;width:240px;font-size:13px">Subscribe to our newsletter to receive updates on the latest news</p>
    <div class="subscribe"><span>Subscribe with us</span><span style="font-size:18px">&rarr;</span></div>
  </div>
  <div class="footer-col" style="left:860px">
    <h4>Contacts</h4>
    <div class="contact-row"><svg width="30" height="30" viewBox="0 0 24 24"><path d="M6 2l4 5-2 3a12 12 0 006 6l3-2 5 4-3 4C10 21 3 14 2 5z" fill="none" stroke="#f6c31a" stroke-width="1.6"/></svg><div><b>Contact Us</b><small>(02) 5550 1842</small></div></div>
    <div class="contact-row"><svg width="30" height="30" viewBox="0 0 24 24"><rect x="3" y="5" width="18" height="14" rx="2" fill="none" stroke="#f6c31a" stroke-width="1.6"/><path d="M3 7l9 6 9-6" fill="none" stroke="#f6c31a" stroke-width="1.6"/></svg><div><b>Mail Us</b><small>hello@plantskillsacademy.com</small></div></div>
  </div>
  <div class="bottom-bar">Southern Plantskills Academy</div>
  <div class="to-top"><svg width="34" height="34" viewBox="0 0 34 34"><path d="M11 20l6-6 6 6" fill="none" stroke="#fff" stroke-width="2"/></svg></div>
</footer>

</body>
</html>
```